Hvac and insulation company needs good looking business card design

We are hvac and insulation company and looking for a new business cards that look to today standards designs

Target Market(s)

homeowners

Industry/Entity Type

Hvac

Contact Information for Business Card

Name: Walter Brinoku
Home comfort consultant
address: 4827 Dunmore St #215 Oakland, CA 94619
office: 888-316-2790
cell: 510-742-3185
Lic.# 584261
Email: walter@corvane-hvac.com
Web: corvane-hvac.com

Requirements
Must have
• clean and sleek look
Nice to have
• simple with a clean look
Should not have
• to busy business card

```html
<!DOCTYPE html>
<html lang="en">
<head>
<meta charset="utf-8">
<title>Corvane – Business Card</title>
<link href="https://fonts.googleapis.com/css2?family=Source+Sans+3:wght@400;600&display=swap" rel="stylesheet">
<style>
  :root {
    --brand-orange: #f2841f;
    --card-white: #f4f4f4;
    --ink: #2b2b2b;
    --ink-muted: #6b6b6b;
    --backdrop: #e6e6e6;
  }
  * { margin: 0; padding: 0; box-sizing: border-box; }
  html, body {
    width: 1200px; height: 900px; overflow: hidden;
    background: var(--backdrop);
    font-family: "Source Sans 3", "Segoe UI", sans-serif;
  }
  .stage { position: relative; width: 1200px; height: 900px; }

  .card {
    position: absolute; top: 200px; width: 308px; height: 502px;
    box-shadow: 2px 3px 5px rgba(0,0,0,0.35);
  }
  .card--front {
    left: 309px; background: var(--card-white);
    border-radius: 52px 0 52px 0;
  }
  .card--back {
    left: 641px; background: var(--brand-orange);
    border-radius: 0 52px 0 52px;
    display: flex; align-items: center; justify-content: center;
  }

  .wordmark {
    position: absolute; left: 24px; top: 78px;
    font-size: 40px; font-weight: 600; letter-spacing: 0.5px;
    color: var(--brand-orange); line-height: 1;
  }
  .wordmark--large {
    position: static; color: #ffffff; font-size: 58px;
  }

  .person { position: absolute; left: 24px; top: 180px; }
  .person__name {
    font-size: 17px; font-weight: 600; color: var(--brand-orange);
    text-transform: uppercase; letter-spacing: 0.3px; line-height: 22px;
  }
  .person__role { font-size: 13.5px; color: var(--ink); line-height: 20px; }

  .contacts { position: absolute; left: 24px; top: 251px; list-style: none; }
  .contacts li {
    display: flex; align-items: center; gap: 7px;
    font-size: 13.5px; color: var(--ink); line-height: 18px;
  }
  .contacts svg { width: 12px; height: 12px; fill: var(--brand-orange); flex: none; }

  .address {
    position: absolute; left: 26px; top: 348px;
    font-style: normal; font-size: 13.5px; color: var(--ink); line-height: 18px;
  }
  .license {
    position: absolute; left: 24px; top: 411px;
    font-size: 13.5px; color: var(--brand-orange);
  }
</style>
</head>
<body>
<main class="stage">
  <section class="card card--front" aria-label="Business card front">
    <div class="wordmark">corvane</div>

    <div class="person">
      <p class="person__name">Walter Brinoku</p>
      <p class="person__role">Home Comfort Consultant</p>
    </div>

    <ul class="contacts">
      <li>
        <svg viewBox="0 0 12 12" aria-hidden="true"><path d="M1 4c0-2 2-3 5-3s5 1 5 3l-2 1-1-2H4L3 5 1 4zM2 6h8l1 5H1z"/></svg>
        888-316-2790
      </li>
      <li>
        <svg viewBox="0 0 12 12" aria-hidden="true"><path d="M3 0h6a1 1 0 0 1 1 1v10a1 1 0 0 1-1 1H3a1 1 0 0 1-1-1V1a1 1 0 0 1 1-1zm0 2v7h6V2z"/></svg>
        510-742-3185
      </li>
      <li>
        <svg viewBox="0 0 12 12" aria-hidden="true"><path d="M0 2h12v8H0zm1 1v.4l5 3.3 5-3.3V3z"/></svg>
        walter@corvane-hvac.com
      </li>
      <li>
        <svg viewBox="0 0 12 12" aria-hidden="true"><circle cx="6" cy="6" r="6"/></svg>
        corvane-hvac.com
      </li>
    </ul>

    <address class="address">4827 Dunmore St #215<br>Oakland, CA 94619</address>

    <p class="license">Lic.# 584261</p>
  </section>

  <section class="card card--back" aria-label="Business card back">
    <div class="wordmark wordmark--large">corvane</div>
  </section>
</main>
</body>
</html>
```